Tech company needs a brochure design

Hi there.

We have written the text for a 4 page brochure, and this needs laying out.

We are in the process of rebranding, and have a new logo, but haven't yet established a colour pallete or design style.

Our current preference is for simple and bold. An example is the current website holding page is marvaxen.io

Colour pallet should pull from the logo for primary colours, but we're open to secondary colours.

The layout in the document is not set in stone, but should be used as a guideline.

The final text is almost ready (we're polishing the phrasing), but it will be almost identical in the number of words and layout.

Target Market(s)

Typically, they are companies that operate in highly regulated industries, such as Financial Services, Telecoms or Healthcare, are data-centric and need to adhere to regulations such as GDPR. Or, data-sensitive, such as Legal, Accountancy or even Retail, where a breach of the network would give access to highly sensitive information.

Regulations and compliance requirements affect the systems they have in place, particularly when it comes to managing and securing data.

All of this impacts the IT infrastructure that is needed, and Marvaxen can provide a seamless network that allows for all the regulations and doesn’t affect the working environment.

Marvaxen sells into these environments at a senior level – IT Director, CIO, CTO.

Industry/Entity Type

Cyber Security

Font styles to use
Sans Serif
Other font styles liked:
• Nexa

Requirements
Must have
• 4 pages in landscape
Clean design
Be appropriate for corporate/business environments but still have vitality
use attached logo for colours - Gray is #2f2f2f
Nice to have
• Can be white or dark based
Should not have
• Not Fussy
Icons that don’t have any relevance

```html
<!DOCTYPE html>
<html lang="en">
<head>
<meta charset="utf-8">
<title>Marvaxen Brochure</title>
<link href="https://fonts.googleapis.com/css2?family=Poppins:wght@300;400;500;600;700&display=swap" rel="stylesheet">
<style>
  :root{
    --grey-dark:#2f2f2f;
    --grey-text:#6b6b6b;
    --bg:#e4e4e4;
    --paper:#f5f5f5;
    --panel:#e9eaeb;
    --red:#c8231f;
    --orange:#e2601f;
    --white:#ffffff;
  }
  *{box-sizing:border-box;margin:0;padding:0}
  html,body{width:1200px;height:2361px;overflow:hidden}
  body{background:var(--bg);font-family:"Poppins",sans-serif;color:var(--grey-dark)}
  .stage{height:787px;display:flex;align-items:center;justify-content:center}
  .spread{display:flex;box-shadow:0 10px 30px rgba(0,0,0,.15)}
  .cover-solo{box-shadow:0 12px 34px rgba(0,0,0,.18);display:block}
  .page{width:540px;height:386px;background:var(--paper);position:relative;overflow:hidden}
  .page + .page{border-left:1px solid #d6d6d6}
  .cover-svg{display:block}

  /* back page */
  .back{padding:24px 26px 0}
  .h-tick{font-size:8.5px;font-weight:600;text-transform:uppercase;letter-spacing:.2px;padding-left:8px;border-left:2px solid var(--red);line-height:1.1;margin-bottom:5px}
  .copy{font-size:6.2px;line-height:1.6;color:var(--grey-text);margin-bottom:10px}
  .ways{background:var(--panel);border-radius:6px;padding:11px 12px;margin:4px 0 12px}
  .ways-title{font-size:10px;font-weight:400;margin-bottom:7px}
  .ways-cols{display:flex;gap:14px}
  .way{flex:1}
  .way-head{font-size:6.2px;font-weight:600;margin-bottom:3px}
  .way-head span{color:var(--orange)}
  .way p{font-size:5.8px;line-height:1.5;color:var(--grey-text)}
  .contact-bar{position:absolute;left:26px;right:26px;bottom:20px;height:50px;display:flex}
  .contact-cta{width:170px;background:var(--grey-dark);color:var(--white);font-size:8.5px;line-height:1.3;padding:9px 14px;border-radius:6px 0 0 6px;clip-path:polygon(0 0,92% 0,100% 50%,92% 100%,0 100%)}
  .contact-info{flex:1;background:linear-gradient(90deg,var(--red),var(--orange));color:var(--white);padding:8px 14px 8px 20px;border-radius:0 6px 6px 0;margin-left:-8px}
  .contact-name{font-size:9px;font-weight:600;margin-bottom:2px}
  .contact-info p{font-size:5.8px;line-height:1.6}

  /* inner pages */
  .inner-left{padding:26px 30px}
  .title{font-size:13px;font-weight:500;line-height:1.15;padding-left:9px;border-left:3px solid var(--red);margin-bottom:6px}
  .lead{font-size:6.2px;color:var(--grey-text);margin-bottom:7px;font-style:italic}
  .stats{position:absolute;left:0;right:0;bottom:34px;height:110px;background:var(--panel);display:flex;justify-content:space-around;align-items:center;padding:0 40px}
  .stat{text-align:center;width:110px}
  .stat svg{display:block;margin:0 auto 4px}
  .stat-num{font-size:26px;font-weight:600;color:var(--red);line-height:1}
  .stat-label{font-size:6.5px;color:var(--grey-text);line-height:1.3;margin-top:3px}
  .inner-right{padding:40px 30px 0 26px}
  .inner-right .copy{width:272px}
  .inner-right .h-tick{font-size:7.5px;text-transform:none;font-weight:500}
  .photo{position:absolute;right:0;bottom:0;width:196px;height:250px;background:linear-gradient(160deg,#f3d4c2 0%,#e9875a 45%,#d4451f 100%)}
</style>
</head>
<body>

<section class="stage">
  <svg class="cover-svg cover-solo" width="800" height="571" viewBox="0 0 700 500">
    <defs>
      <linearGradient id="paperA" x1="0" y1="0" x2="1" y2="1"><stop offset="0" stop-color="#f6f6f6"/><stop offset="1" stop-color="#d8d8d8"/></linearGradient>
      <linearGradient id="artA" x1="0" y1="1" x2="1" y2="0"><stop offset="0" stop-color="#c8231f" stop-opacity=".55"/><stop offset=".45" stop-color="#f1e1dc"/><stop offset="1" stop-color="#e2601f" stop-opacity=".45"/></linearGradient>
      <linearGradient id="leadA" x1="0" y1="0" x2="0" y2="1"><stop offset="0" stop-color="#f4b8a6"/><stop offset="1" stop-color="#e9e4e2"/></linearGradient>
    </defs>
    <rect width="700" height="500" fill="url(#paperA)"/>
    <rect x="90" y="150" width="270" height="350" fill="url(#artA)" role="img" aria-label="Red-orange swoosh with a formation of white paper planes flying upward"/>
    <rect x="400" y="90" width="100" height="140" fill="url(#leadA)" role="img" aria-label="Red paper plane leading ahead along a dashed flight trail"/>
    <text x="40" y="120" font-family="Poppins, sans-serif" font-size="40" font-weight="600" fill="#2f2f2f">Marvaxen</text>
    <g font-family="Poppins, sans-serif" text-anchor="end" fill="#2f2f2f">
      <text x="665" y="264" font-size="17" font-weight="300">Propelling clients</text>
      <text x="665" y="288" font-size="17" font-weight="300">through the journey to efficiency</text>
      <text x="665" y="330" font-size="23" font-weight="600">CHANGE YOUR THINKING</text>
      <text x="665" y="362" font-size="23" font-weight="600">CHANGE YOUR APPROACH</text>
      <text x="665" y="394" font-size="23" font-weight="600">REAP THE REWARDS</text>
    </g>
  </svg>
</section>

<section class="stage">
  <div class="spread">
    <article class="page back">
      <h2 class="h-tick">Structuring your business in the right way</h2>
      <p class="copy">Budgets are tight, technology and security teams need to do more with less, whilst the business requires an ever-increasing array of new technologies to stay ahead of the competition. Marvaxen provides a holistic wrapper around people, processes and technology to create a more efficient organisation that operates and runs more effectively, enabling you to deliver products and services to market faster while enhancing the customer experience.</p>
      <h2 class="h-tick">Propelling your technology journey</h2>
      <p class="copy">Every organisation is different. Requirements differ, structures contrast and objectives vary. One size does not fit all and an all encompassing view is essential to start the journey from the correct point and achieve the desired outcome.<br>At Marvaxen, we consider our client's entire eco-system. By understanding the nuances of compliance obligations, employee practice, technical complexities and process requirements, we redefine the problem to build the solution that will drive your business forward.</p>
      <div class="ways">
        <p class="ways-title">There are several ways we work with our clients.</p>
        <div class="ways-cols">
          <div class="way"><p class="way-head">Manage the journey <span>For You</span></p><p>Marvaxen takes control and full responsibility, so you don't have to worry. We manage the risk. You gain the results and the desired outcome.</p></div>
          <div class="way"><p class="way-head">Go on the journey <span>With You</span></p><p>We work in partnership with you, enhancing your existing team and upskilling your capabilities along the way.</p></div>
          <div class="way"><p class="way-head">The journey is taken <span>By You</span></p><p>Marvaxen provide you with the right tools to make the journey yourself.</p></div>
        </div>
      </div>
      <h2 class="h-tick">Your peace of mind is essential</h2>
      <p class="copy">Building trust and working in partnership with our clients is important to us. Marvaxen follows a framework-led, principle-based approach, with a unique methodology, and has extensive technical expertise across the leading technologies in the market.</p>
      <div class="contact-bar">
        <div class="contact-cta">Contact us today to talk about setting your business on the journey to efficiency</div>
        <div class="contact-info">
          <p class="contact-name">Marvaxen</p>
          <p>E: info@marvaxen.io &nbsp;|&nbsp; W: marvaxen.io &nbsp;|&nbsp; T: +44 (0)1632 960418</p>
          <p>Unit 7 | Elm Court | Station Road | Harwell | Oxfordshire | OX11 4QT</p>
        </div>
      </div>
    </article>
    <div class="page">
      <svg class="cover-svg" width="540" height="386" viewBox="0 0 700 500">
        <defs>
          <linearGradient id="paperB" x1="0" y1="0" x2="1" y2="1"><stop offset="0" stop-color="#f6f6f6"/><stop offset="1" stop-color="#d8d8d8"/></linearGradient>
          <linearGradient id="artB" x1="0" y1="1" x2="1" y2="0"><stop offset="0" stop-color="#c8231f" stop-opacity=".55"/><stop offset=".45" stop-color="#f1e1dc"/><stop offset="1" stop-color="#e2601f" stop-opacity=".45"/></linearGradient>
          <linearGradient id="leadB" x1="0" y1="0" x2="0" y2="1"><stop offset="0" stop-color="#f4b8a6"/><stop offset="1" stop-color="#e9e4e2"/></linearGradient>
        </defs>
        <rect width="700" height="500" fill="url(#paperB)"/>
        <rect x="90" y="150" width="270" height="350" fill="url(#artB)" role="img" aria-label="Red-orange swoosh with a formation of white paper planes flying upward"/>
        <rect x="400" y="90" width="100" height="140" fill="url(#leadB)" role="img" aria-label="Red paper plane leading ahead along a dashed flight trail"/>
        <text x="40" y="120" font-family="Poppins, sans-serif" font-size="40" font-weight="600" fill="#2f2f2f">Marvaxen</text>
        <g font-family="Poppins, sans-serif" text-anchor="end" fill="#2f2f2f">
          <text x="665" y="264" font-size="17" font-weight="300">Propelling clients</text>
          <text x="665" y="288" font-size="17" font-weight="300">through the journey to efficiency</text>
          <text x="665" y="330" font-size="23" font-weight="600">CHANGE YOUR THINKING</text>
          <text x="665" y="362" font-size="23" font-weight="600">CHANGE YOUR APPROACH</text>
          <text x="665" y="394" font-size="23" font-weight="600">REAP THE REWARDS</text>
        </g>
      </svg>
    </div>
  </div>
</section>

<section class="stage">
  <div class="spread">
    <article class="page inner-left">
      <h2 class="title">A Different Provider<br>A Different Type of Business Solution</h2>
      <p class="lead">We are Marvaxen. We have been propelling companies on the journey to automation and efficiency since 2005.</p>
      <p class="copy">Our expertise lies in modernising, automating and securing complex technical environments. By balancing the requirements of compliance with the realities of technology, process and people, we establish a clean, compliant and secure business setting for our clients, one that is robust, easy to run, straightforward to maintain and effortless to adapt and scale.</p>
      <p class="copy">We are different from others in our approach. In listening to our clients and applying Marvaxen's unique methodology, we look across the whole environment and challenge the existing way of doing things. Our approach means we streamline people, process and technology in the most appropriate fashion, to deliver comprehensive and secure solutions that propel our clients toward digital business efficiency.</p>
      <p class="copy">In providing our clients with an efficient, secure and compliant environment, productivity improvements are recognised, technology spend is optimised, whilst costs and risk are reduced. With your company operating in a streamlined manner, services are improved and the customer experience is delivered to establish competitive advantage in the market.</p>
      <div class="stats">
        <div class="stat">
          <svg width="22" height="22" viewBox="0 0 22 22"><circle cx="11" cy="11" r="6" fill="none" stroke="#2f2f2f" stroke-width="1.4" stroke-dasharray="3 1.5"/><circle cx="11" cy="11" r="2.5" fill="none" stroke="#2f2f2f" stroke-width="1.2"/></svg>
          <p class="stat-num">84%</p><p class="stat-label">More efficient IT<br>operations</p>
        </div>
        <div class="stat">
          <svg width="22" height="22" viewBox="0 0 22 22"><circle cx="12" cy="12" r="7" fill="none" stroke="#2f2f2f" stroke-width="1.3"/><path d="M12 12 L12 7 M10 3 H14" stroke="#2f2f2f" stroke-width="1.3"/></svg>
          <p class="stat-num">92%</p><p class="stat-label">Increase in speed of<br>execution &amp; delivery</p>
        </div>
        <div class="stat">
          <svg width="22" height="22" viewBox="0 0 22 22"><circle cx="11" cy="11" r="8" fill="none" stroke="#2f2f2f" stroke-width="1.3"/><text x="11" y="14.5" text-anchor="middle" font-size="10" font-family="Poppins, sans-serif" fill="#2f2f2f">£</text></svg>
          <p class="stat-num">60%</p><p class="stat-label">Reduction in costs<br>to the business</p>
        </div>
      </div>
    </article>
    <article class="page inner-right">
      <h2 class="h-tick">The Changing Landscape</h2>
      <p class="copy">Today's fast-paced business environment is a complex world. Technology and the way that people consume information is evolving at speed and continuously changing. Most organisations have evolved over time and often consist of legacy technologies, added incrementally, making them hard to adapt and time-consuming to manage. This operational complexity, driven by the need to adhere to current compliance and ever-changing working practices, is only increasing the pressure on already strained resources.</p>
      <p class="copy">These are the environments where Marvaxen excels. We streamline and automate the IT estate, rationalising and securing technology, processes and systems. We propel our clients towards the digital, secure and compliant environment needed for business success.</p>
      <h2 class="h-tick">Digital Efficiency</h2>
      <p class="copy">An efficient digital environment will establish competitive advantage in this interconnected world. People, process and technology need to be streamlined and Marvaxen are experts in unifying and refining this environment. By merging our unique methodology with market-leading technologies, Marvaxen will deliver you digital efficiency that drives your competitive advantage.</p>
      <h2 class="h-tick">Governance, Risk &amp; Compliance</h2>
      <p class="copy">Data is often the lifeblood of companies and regulations abound. Making sense of this environment and protecting sensitive information, whether that's client or corporate data, is fundamental. Marvaxen can identify your risk profile and pinpoint areas of concern, guiding you in establishing good governance around policy, procedures and technology use.</p>
      <div class="photo" role="img" aria-label="Orange-toned photo of a businessman holding a tablet showing charts, blended with a city skyline"></div>
    </article>
  </div>
</section>

</body>
</html>
```